Business Card Design for BrightvaleMedia.com

--I need a business card design for my company BrightvaleMedia.com

I have attached my logo...I want the brightvale media logo on the front of the business card, and then I want The Quillstone Chief on the back of it with my information.

I would like to see a light colored background as well as a dark colored background

FRONT:
BRIGHTVALE MEDIA LOGO
248 N. Larkmoor
3rd Floor
San Diego CA 92173
www.BrightvaleMedia.com

Advanced Website & App Development
Websites, Apps, Online Voucher Systems

Leading Edge Marketing Services
SMS, VB, SMM, SEM,

BACK:
QUILLSTONE CHIEF LOGO
Dorian Pelletta
The Quillstone Chief
Call Or Text: 619-555-0148
Dorian@QuillstoneChief.example
www.QuillstoneChief.example

Target Market(s)

small business owners

Industry/Entity Type

Business Consultant

Contact Information for Business Card

FRONT:
BRIGHTVALE MEDIA LOGO
248 N. Larkmoor
3rd Floor
San Diego CA 92173
www.BrightvaleMedia.com

SMS, VB, SMM, SEM,

BACK:
QUILLSTONE CHIEF LOGO
Dorian Pelletta
The Quillstone Chief
Dorian@QuillstoneChief.example
www.QuillstoneChief.example

Requirements
Must have
• add this quote on it somewhere, anywhere,preferrably on back
• "The Fastest Way To Success Is To Take Action”
• — Dorian Pelletta, Quillstone Chief
Nice to have
• open
Should not have
• red

```html
<!DOCTYPE html>
<html lang="en">
<head>
<meta charset="utf-8">
<title>Brightvale Media – Business Cards</title>
<link rel="stylesheet" href="https://fonts.googleapis.com/css2?family=Open+Sans:wght@400;600;700&display=swap">
<style>
  :root {
    --backdrop: #4a4a4a;
    --card-light: #ffffff;
    --card-dark: #0b6fa8;
    --brand-blue: #1470ab;
    --text-grey: #555555;
    --text-white: #ffffff;
    --text-soft: rgba(255, 255, 255, 0.85);
  }
  * { margin: 0; padding: 0; box-sizing: border-box; }
  html, body {
    width: 1105px;
    height: 1200px;
    overflow: hidden;
    background: var(--backdrop);
    font-family: "Open Sans", Arial, sans-serif;
  }
  .canvas { position: relative; width: 1105px; height: 1200px; }
  .card {
    position: absolute;
    left: 196px;
    width: 719px;
    height: 411px;
  }
  .card--front { top: 146px; background: var(--card-light); color: var(--text-grey); text-align: center; }
  .card--back { top: 602px; background: var(--card-dark); color: var(--text-white); }

  .front-logo {
    position: absolute; left: 0; right: 0; top: 86px;
    font-size: 34px; font-weight: 600; letter-spacing: 3px;
    color: var(--brand-blue);
  }
  .front-info { position: absolute; left: 0; right: 0; top: 172px; font-size: 19px; line-height: 26px; }
  .front-info .url { color: var(--brand-blue); font-weight: 700; }
  .front-info .group { margin-top: 14px; }
  .front-info .dot { color: var(--brand-blue); }

  .back-logo {
    position: absolute; right: 60px; top: 58px;
    font-size: 40px; font-weight: 600; letter-spacing: 3px;
    color: var(--text-white);
  }
  .accent-bar { position: absolute; left: 0; top: 215px; width: 14px; height: 153px; background: var(--text-white); }
  .profile { position: absolute; left: 58px; top: 212px; }
  .profile-name { font-size: 26px; font-weight: 600; line-height: 34px; }
  .profile-title { font-size: 20px; line-height: 28px; }
  .contact-list { list-style: none; margin-top: 14px; }
  .contact-list li { display: flex; align-items: center; font-size: 19px; line-height: 27.5px; white-space: nowrap; }
  .contact-list svg { width: 17px; height: 17px; margin-right: 12px; flex: none; }

  .motto {
    position: absolute; right: 40px; bottom: 44px; width: 270px;
    text-align: right; color: var(--text-soft);
  }
  .motto-text { font-size: 15px; line-height: 21px; }
  .motto-source { margin-top: 6px; font-size: 13px; line-height: 18px; }
</style>
</head>
<body>
<main class="canvas">
  <section class="card card--front" aria-label="Card front">
    <div class="front-logo">BRIGHTVALE MEDIA</div>
    <div class="front-info">
      <p>248 N. Larkmoor, 3rd Floor, San Diego CA 92173</p>
      <p class="url">www.BrightvaleMedia.com</p>
      <div class="group">
        <p>Advanced Website &amp; App Development</p>
        <p>Websites <span class="dot">•</span> Apps <span class="dot">•</span> Online Voucher Systems</p>
      </div>
      <div class="group">
        <p>Leading Edge Marketing Services</p>
        <p>SMS <span class="dot">•</span> VB <span class="dot">•</span> SMM <span class="dot">•</span> SEM</p>
      </div>
    </div>
  </section>

  <section class="card card--back" aria-label="Card back">
    <div class="back-logo">QUILLSTONE CHIEF</div>
    <div class="accent-bar"></div>
    <div class="profile">
      <p class="profile-name">Dorian Pelletta</p>
      <p class="profile-title">The Quillstone Chief</p>
      <ul class="contact-list">
        <li>
          <svg viewBox="0 0 24 24" aria-hidden="true"><path fill="#fff" d="M6.6 10.8a15.1 15.1 0 0 0 6.6 6.6l2.2-2.2c.3-.3.7-.4 1-.2 1.1.4 2.3.6 3.6.6.6 0 1 .4 1 1V20c0 .6-.4 1-1 1A17 17 0 0 1 3 4c0-.6.4-1 1-1h3.5c.6 0 1 .4 1 1 0 1.3.2 2.5.6 3.6.1.3 0 .7-.2 1z"/></svg>
          619-555-0148
        </li>
        <li>
          <svg viewBox="0 0 24 24" aria-hidden="true"><rect x="2" y="5" width="20" height="14" rx="1.5" fill="#fff"/><path d="M3 6l9 7 9-7" fill="none" stroke="#0b6fa8" stroke-width="1.8"/></svg>
          Dorian@QuillstoneChief.example
        </li>
        <li>
          <svg viewBox="0 0 24 24" aria-hidden="true"><circle cx="12" cy="12" r="10" fill="#fff"/><path d="M7 7c2 1 3 0 4 2s-1 3 1 4 1 4 2 5M15 5c-1 2 1 3 3 3" fill="none" stroke="#0b6fa8" stroke-width="1.8"/></svg>
          www.QuillstoneChief.example
        </li>
      </ul>
    </div>
    <blockquote class="motto">
      <p class="motto-text">“The Fastest Way To Success Is To Take Action”</p>
      <p class="motto-source">— Dorian Pelletta, Quillstone Chief</p>
    </blockquote>
  </section>
</main>
</body>
</html>
```